A private security company called "Tavron Security Services Ltd"

Hello everybody,

We need a web page for a company based in NZ. It is mainly an informative website so it would be wonderful if the designer puts their absolute best into making it a website that I would really appreciate. The website needs to show professionalism and also needs to make our web surfers find the information they need in a click. the company's colour is black and silver, and if those two colours could be integrated into the website it would be absolutely lovely. Please do contact me for any information.

Sincerely,
Dorian Vaskel

Industry/Entity Type

Security

```html
<!DOCTYPE html>
<html lang="en">
<head>
<meta charset="utf-8">
<title>Tavron Security Services Ltd</title>
<link href="https://fonts.googleapis.com/css2?family=Roboto:wght@300;400;500;700&display=swap" rel="stylesheet">
<style>
:root{
  --orange:#f5b231;
  --ink:#2f3237;
  --slate:#3d424a;
  --grey-text:#5a5d62;
  --white:#ffffff;
  --nav-top:#4a4b4d;
  --nav-bottom:#1f2022;
  --hero-a:#dfe7f1;
  --hero-b:#8fa8c3;
}
*{margin:0;padding:0;box-sizing:border-box}
html,body{width:889px;height:1200px;overflow:hidden;background:var(--white)}
body{font-family:'Roboto',sans-serif;color:var(--ink);position:relative}

.header{position:absolute;left:0;top:0;width:889px;height:94px}
.contact{position:absolute;top:50px;font-size:13px;display:flex;align-items:center;gap:8px;color:var(--ink)}
.contact.email{left:128px}
.contact.phone{right:139px}
.brand{position:absolute;left:0;width:889px;top:50px;display:flex;justify-content:center;align-items:center;gap:8px}
.brand-mark{width:12px;height:12px;background:var(--ink)}
.brand-name{font-weight:700;color:var(--ink);line-height:1.1;text-align:center}
.brand-name .word{display:block;font-size:18px;letter-spacing:2px}
.brand-name .sub{display:block;font-size:7.5px;letter-spacing:.3px}

.nav{position:absolute;left:0;top:94px;width:889px;height:46px;background:linear-gradient(var(--nav-top),var(--nav-bottom))}
.nav ul{list-style:none;display:flex;position:absolute;left:127px;top:0;height:46px}
.nav li{height:46px;line-height:46px;font-size:11.2px;color:var(--white);padding:0 14px;border-right:1px solid #5b5c5e;white-space:nowrap}
.nav li:last-child{border-right:none}
.nav li.active{background:var(--orange);padding:0 17px;border-right:none}

.hero{position:absolute;left:0;top:140px;width:889px;height:383px;background:linear-gradient(100deg,var(--hero-a) 0%,#c3d2e3 45%,var(--hero-b) 100%)}
.hero-title{position:absolute;left:135px;top:200px;font-size:23px;line-height:32px;color:#1f2226;font-weight:400}
.btn{display:block;background:var(--orange);color:var(--white);text-align:center;border-radius:2px}
.hero-btn{position:absolute;left:135px;top:271px;width:133px;height:36px;line-height:36px;font-size:15px}
.hero-arrows{position:absolute;left:288px;top:275px}

.services{position:absolute;left:0;top:523px;width:889px;height:265px}
.section-title{position:absolute;left:128px;top:30px;font-size:15.5px;font-weight:400;color:var(--ink)}
.mini-arrows{position:absolute;left:718px;top:29px;display:flex;gap:2px}
.mini-arrows span{width:16px;height:16px;background:var(--orange);display:flex;align-items:center;justify-content:center}
.card{position:absolute;top:64px;width:150px;text-align:center}
.card .thumb{width:150px;height:113px;border:1px solid #d8d8d8}
.card h3{margin-top:13px;font-size:12px;font-weight:400;color:var(--orange)}
.card p{margin-top:6px;font-size:10px;line-height:15px;color:var(--grey-text)}

.welcome{position:absolute;left:0;top:788px;width:889px;height:207px;background:var(--slate)}
.welcome .photo{position:absolute;left:129px;top:34px;width:277px;height:141px;background:linear-gradient(120deg,#cfe0f0 0%,#6f9ac6 45%,#1c1f24 60%,#2a2d33 100%)}
.welcome h2{position:absolute;left:422px;top:33px;font-size:17px;font-weight:400;color:var(--orange)}
.welcome .lead{position:absolute;left:424px;top:60px;font-size:10.6px;color:var(--white)}
.welcome .body{position:absolute;left:422px;top:90px;width:339px;font-size:10px;line-height:17.6px;color:#e6e7e9;text-align:justify}
.welcome .btn{position:absolute;left:675px;top:151px;width:86px;height:23px;line-height:23px;font-size:10.5px}

.links{position:absolute;left:0;top:995px;width:889px;height:139px}
.col{position:absolute;top:30px}
.col h4{font-size:10.5px;font-weight:400;color:var(--ink);margin-bottom:14px}
.col ul{list-style:none}
.col li{font-size:10.2px;color:var(--ink);height:19.6px;display:flex;align-items:center;gap:6px}

.footer{position:absolute;left:0;top:1134px;width:889px;height:66px;background:var(--slate)}
.footer .legal{position:absolute;left:130px;top:28px;font-size:10.5px;color:var(--white)}
.social{position:absolute;left:655px;top:20px;display:flex;gap:5px}
.social span{width:22px;height:22px;border-radius:50%;background:#53585f}
</style>
</head>
<body>

<header class="header">
  <div class="contact email">
    <svg width="20" height="14" viewBox="0 0 20 14"><rect width="20" height="14" rx="1" fill="#f5b231"/><path d="M1 1l9 7 9-7" stroke="#fff" stroke-width="1.6" fill="none"/></svg>
    info@tavronsecurity.co.nz
  </div>
  <div class="brand">
    <span class="brand-mark"></span>
    <div class="brand-name"><span class="word">TAVRON</span><span class="sub">SECURITY SERVICES LTD.</span></div>
  </div>
  <div class="contact phone">
    <svg width="16" height="20" viewBox="0 0 16 20"><rect x="0" y="0" width="5" height="20" rx="1" fill="#f5b231"/><rect x="6" y="4" width="10" height="16" rx="1" fill="#f5b231"/><g fill="#fff"><rect x="8" y="6" width="6" height="3"/><rect x="8" y="11" width="2" height="2"/><rect x="12" y="11" width="2" height="2"/><rect x="8" y="15" width="2" height="2"/><rect x="12" y="15" width="2" height="2"/></g></svg>
    +64-9-555-0142
  </div>
</header>

<nav class="nav">
  <ul>
    <li class="active">Home</li>
    <li>Security Guards</li>
    <li>Security Patrols</li>
    <li>Access Control</li>
    <li>Tavron Security Careers</li>
    <li>About Us</li>
    <li>Contact Us</li>
  </ul>
</nav>

<section class="hero" role="img" aria-label="Close-up of a mounted CCTV surveillance camera against a soft blue sky">
  <h1 class="hero-title">PROFESSIONAL POWERFUL<br>SECURITY PROTECTION</h1>
  <a class="btn hero-btn">MORE INFO</a>
  <svg class="hero-arrows" width="44" height="28" viewBox="0 0 44 28"><path d="M14 1L2 14l12 13M30 1l12 13-12 13" stroke="#fff" stroke-width="1.6" fill="none"/></svg>
</section>

<section class="services">
  <h2 class="section-title">SERVICES WE PROVIDE</h2>
  <div class="mini-arrows">
    <span><svg width="8" height="10"><path d="M6 1L2 5l4 4" stroke="#fff" stroke-width="1.4" fill="none"/></svg></span>
    <span><svg width="8" height="10"><path d="M2 1l4 4-4 4" stroke="#fff" stroke-width="1.4" fill="none"/></svg></span>
  </div>
  <div class="card" style="left:127px">
    <div class="thumb" role="img" aria-label="Hand pressing a home alarm keypad" style="background:linear-gradient(135deg,#f2f2f2,#d9d9d9)"></div>
    <h3>HOME SECURITY</h3>
    <p>Mes cuml dia sed in lacus ut<br>eniascet ingerto aliiqt es site</p>
  </div>
  <div class="card" style="left:287px">
    <div class="thumb" role="img" aria-label="Two uniformed guards patrolling a city square" style="background:linear-gradient(180deg,#8fb3dc,#6d7a86 60%,#4a4d52)"></div>
    <h3>BUSINESS SECURITY</h3>
    <p>Mes cuml dia sed in lacus ut<br>eniascet ingerto aliiqt es site</p>
  </div>
  <div class="card" style="left:447px">
    <div class="thumb" role="img" aria-label="Security officer's belt with baton" style="background:linear-gradient(90deg,#b9a9a3,#5b6a85 55%,#2c3548)"></div>
    <h3>SECURITY FOR KIDS</h3>
    <p>Mes cuml dia sed in lacus ut<br>eniascet ingerto aliiqt es site</p>
  </div>
  <div class="card" style="left:608px">
    <div class="thumb" role="img" aria-label="Blue-toned security camera hardware" style="background:linear-gradient(135deg,#f4f7fc,#b8c9ea 60%,#4d6fc0)"></div>
    <h3>HARDWARE SYSTEM</h3>
    <p>Mes cuml dia sed in lacus ut<br>eniascet ingerto aliiqt es site</p>
  </div>
</section>

<section class="welcome">
  <div class="photo" role="img" aria-label="Guard in a black security shirt seen from behind against a blue sky"></div>
  <h2>WELCOME TO TSS</h2>
  <p class="lead">Mes cuml dia sed inenias ingerto lot aliiqtes dolore ipsum commete</p>
  <p class="body">Mes cuml dia sed in lacus ut eniascet ingerto aliiqt es site amet eismod ictor ut ligulate ameti dapibus ticdu nt mtsen lusto dolor ltissim com. Mes cuml dia sed inertio lacusuei ascet dolingerto aliiqt sit amet eism com odictor ut ligulate cot.</p>
  <a class="btn">VIEW MORE</a>
</section>

<section class="links">
  <div class="col" style="left:128px">
    <h4>SECURITY GUARDS</h4>
    <ul>
      <li><svg width="10" height="10"><circle cx="5" cy="5" r="5" fill="#f5b231"/><path d="M2.5 5l2 2 3-3.5" stroke="#fff" stroke-width="1.3" fill="none"/></svg>Site Guards</li>
      <li><svg width="10" height="10"><circle cx="5" cy="5" r="5" fill="#f5b231"/><path d="M2.5 5l2 2 3-3.5" stroke="#fff" stroke-width="1.3" fill="none"/></svg>Concierge Services</li>
      <li><svg width="10" height="10"><circle cx="5" cy="5" r="5" fill="#f5b231"/><path d="M2.5 5l2 2 3-3.5" stroke="#fff" stroke-width="1.3" fill="none"/></svg>Corporate Events</li>
    </ul>
  </div>
  <div class="col" style="left:293px">
    <h4>SECURITY PATROLS</h4>
    <ul>
      <li><svg width="10" height="10"><circle cx="5" cy="5" r="5" fill="#f5b231"/><path d="M2.5 5l2 2 3-3.5" stroke="#fff" stroke-width="1.3" fill="none"/></svg>Scheduled &amp; Random Patrols</li>
      <li><svg width="10" height="10"><circle cx="5" cy="5" r="5" fill="#f5b231"/><path d="M2.5 5l2 2 3-3.5" stroke="#fff" stroke-width="1.3" fill="none"/></svg>Alarm Response</li>
    </ul>
  </div>
  <div class="col" style="left:473px">
    <h4>ALARMS</h4>
    <ul>
      <li><svg width="10" height="10"><circle cx="5" cy="5" r="5" fill="#f5b231"/><path d="M2.5 5l2 2 3-3.5" stroke="#fff" stroke-width="1.3" fill="none"/></svg>Alarm Response</li>
      <li><svg width="10" height="10"><circle cx="5" cy="5" r="5" fill="#f5b231"/><path d="M2.5 5l2 2 3-3.5" stroke="#fff" stroke-width="1.3" fill="none"/></svg>Alarm Monitoring</li>
      <li><svg width="10" height="10"><circle cx="5" cy="5" r="5" fill="#f5b231"/><path d="M2.5 5l2 2 3-3.5" stroke="#fff" stroke-width="1.3" fill="none"/></svg>Alarm Installation</li>
    </ul>
  </div>
  <div class="col" style="left:624px">
    <h4>ACCESS CONTROL SYSTEMS</h4>
    <ul>
      <li><svg width="10" height="10"><circle cx="5" cy="5" r="5" fill="#f5b231"/><path d="M2.5 5l2 2 3-3.5" stroke="#fff" stroke-width="1.3" fill="none"/></svg>Alarm Installation</li>
      <li><svg width="10" height="10"><circle cx="5" cy="5" r="5" fill="#f5b231"/><path d="M2.5 5l2 2 3-3.5" stroke="#fff" stroke-width="1.3" fill="none"/></svg>Security Guards</li>
    </ul>
  </div>
</section>

<footer class="footer">
  <p class="legal">TSS © 2014 PRIVACY POLICY</p>
  <div class="social" aria-label="Social links">
    <span></span><span></span><span></span><span></span>
  </div>
</footer>

</body>
</html>
```